Trade Show Marlow 3x3 booth schel scheme

We would like to have full coverage design for 3x3 booth scheel

2x2 pop up Counter (1200mm wide x 900mm high x 400mm deep)
Our company provides food safety training, consultancy and food safety app service for hospitality businesses.

```html
<!DOCTYPE html>
<html lang="en">
<head>
<meta charset="utf-8">
<title>Marlow – Booth Banner</title>
<link href="https://fonts.googleapis.com/css2?family=Montserrat:wght@500;600;700&display=swap" rel="stylesheet">
<style>
  :root {
    --bg: #2e2e2e;
    --bg-deep: #262626;
    --lime: #cdd42f;
    --white: #ffffff;
    --ink: #1f1f1f;
  }
  * { margin: 0; padding: 0; box-sizing: border-box; }
  html, body { width: 1200px; height: 636px; overflow: hidden; background: var(--bg); }
  .banner {
    position: relative;
    width: 1200px;
    height: 636px;
    font-family: "Montserrat", sans-serif;
    color: var(--white);
  }
  .banner__texture {
    position: absolute; inset: 0;
    background: radial-gradient(ellipse at 50% 45%, #333333 0%, var(--bg) 55%, var(--bg-deep) 100%);
  }
  .brand-dot {
    position: absolute;
    width: 124px; height: 124px;
    top: 261px;
    border-radius: 50%;
    background: var(--lime);
  }
  .brand-dot--left { left: 78px; }
  .brand-dot--right { left: 1000px; }
  .wordmark {
    position: absolute;
    top: 52px; left: 0; width: 1200px;
    text-align: center;
    font-weight: 600;
    font-size: 84px;
    letter-spacing: 0.14em;
    text-indent: 0.14em;
    line-height: 1;
  }
  .rule {
    position: absolute;
    top: 172px; left: 372px;
    width: 457px; height: 2px;
    background: var(--white);
  }
  .headline {
    position: absolute;
    top: 205px; left: 0; width: 1200px;
    text-align: center;
    font-weight: 600;
    font-size: 37px;
    line-height: 59px;
    letter-spacing: 0.1em;
    text-indent: 0.1em;
  }
  .services { position: absolute; inset: 0; }
  .service {
    position: absolute;
    top: 340px;
    width: 200px;
    margin-left: -100px;
    text-align: center;
  }
  .service__icon { display: block; margin: 0 auto; width: 110px; height: 100px; }
  .service__label {
    display: block;
    margin-top: 8px;
    font-weight: 600;
    font-size: 20px;
    letter-spacing: 0.01em;
  }
  .divider {
    position: absolute;
    top: 350px;
    width: 2px; height: 122px;
    background: var(--white);
  }
  .url-pill {
    position: absolute;
    top: 546px; left: 432px;
    width: 336px; height: 47px;
    border-radius: 24px;
    background: var(--white);
    color: var(--ink);
    font-weight: 600;
    font-size: 19px;
    line-height: 47px;
    text-align: center;
  }
</style>
</head>
<body>
<main class="banner">
  <div class="banner__texture" role="img" aria-label="Faint dark botanical pattern of leaves and flower heads"></div>

  <span class="brand-dot brand-dot--left"></span>
  <span class="brand-dot brand-dot--right"></span>

  <h1 class="wordmark">MARLOW</h1>
  <div class="rule"></div>

  <h2 class="headline">FOOD HYGIENE AND<br>HEALTH SAFETY</h2>

  <section class="services">
    <div class="service" style="left:377px;">
      <svg class="service__icon" viewBox="0 0 110 100" aria-hidden="true">
        <circle cx="68" cy="34" r="32" fill="var(--lime)"/>
        <g fill="none" stroke="#fff" stroke-width="2.5" stroke-linecap="round">
          <rect x="26" y="14" width="52" height="38" rx="2"/>
          <line x1="40" y1="24" x2="70" y2="24"/>
          <line x1="40" y1="32" x2="70" y2="32"/>
          <line x1="40" y1="40" x2="62" y2="40"/>
          <line x1="52" y1="52" x2="52" y2="64"/>
          <line x1="52" y1="64" x2="40" y2="78"/>
          <line x1="52" y1="64" x2="64" y2="78"/>
        </g>
      </svg>
      <span class="service__label">Training</span>
    </div>

    <div class="divider" style="left:480px;"></div>

    <div class="service" style="left:598px;">
      <svg class="service__icon" viewBox="0 0 110 100" aria-hidden="true">
        <circle cx="68" cy="34" r="32" fill="var(--lime)"/>
        <g fill="none" stroke="#fff" stroke-width="2.5" stroke-linejoin="round" stroke-linecap="round">
          <path d="M24 18 h38 a4 4 0 0 1 4 4 v22 a4 4 0 0 1 -4 4 h-22 l-10 10 v-10 h-6 a4 4 0 0 1 -4 -4 v-22 a4 4 0 0 1 4 -4 z"/>
          <line x1="32" y1="29" x2="56" y2="29"/>
          <line x1="32" y1="37" x2="50" y2="37"/>
        </g>
      </svg>
      <span class="service__label">Consultancy</span>
    </div>

    <div class="divider" style="left:717px;"></div>

    <div class="service" style="left:835px;">
      <svg class="service__icon" viewBox="0 0 110 100" aria-hidden="true">
        <circle cx="68" cy="34" r="32" fill="var(--lime)"/>
        <g fill="none" stroke="#fff" stroke-width="2.5" stroke-linejoin="round" stroke-linecap="round">
          <rect x="34" y="8" width="36" height="64" rx="6"/>
          <line x1="48" y1="64" x2="56" y2="64"/>
          <path d="M42 36 l7 8 l14 -16"/>
        </g>
      </svg>
      <span class="service__label">Safety App</span>
    </div>
  </section>

  <div class="url-pill">www.marlowsolutions.co.uk</div>
</main>
</body>
</html>
```